Verpackungsdesign für Wellness- und Saunaprodukte
Zielgruppe
BaFinn ist ein junges Start-Up, das sich auf Wellness- und Saunaprodukte spezialisiert hat. Unsere Zielgruppe besteht zu beinahe gleichen Teilen aus männlichen und weiblichen Personen zwischen 30 und 60 Jahren. Unsere Produkte befinden sich eher im mittel- bis höherpreisigen Segment, daher streben wir ein hochwertiges Design für unsere Verpackungen an. Unsere Produktpalette reicht von Mentholkristallen, Saunaaufgüssen, bis hin zu Textilien für den Wellnessbereich und soll dementsprechend Menschen ansprechen, die sich einen gewissen Luxus im Alltag auch gönnen.
Aufgabenstellung
Inspiriert von der skandinavischen Sauna Kultur, möchten wir Momente der Erholung und
Entspannung in den Alltag unserer Kunden bringen. Die Geschichte des Saunierens ist eng mit der skandinavischen Kultur verbunden und skandinavische Stilelemente sind zeitgemäß und sprechen ein breites Publikum an. Das Design muss auf Dosen/Tiegel , Karton Verpackungen und Flaschen verschiedener Größen adaptierbar sein (siehe Bild im Anhang).
40g Tiegel(transparent) Höhe 40mm Durchmesser 60mm (ohne Deckel Silber gebürstet)
100g Tiegel(transparent) Höhe 53mm Durchmesser 71mm (ohne Deckel Silber gebürstet)
200g Tiegel(transparent) Höhe 65mm Durchmesser 90mm (ohne Deckel Silber gebürstet)
Karton Verpackung 124,5x49x49mm
Karton Verpackung 100x100x100mm
Flaschenetikett 134x67mm (Braunglas, schwarzer Deckel)
Es soll ein passendes Keyvisual erstellt werden.
Im Anhang sieht man die Verpackungen, Dosen, Flaschen sowie unsere ersten Design Entwürfe (an diese Anordnung der Elemente kann sich der Designer orientieren ). Das Logo bleibt wie gegeben. Das Produkt für die Tiegel soll Mentholkristalle sein.

```html
<!DOCTYPE html>
<html lang="de">
<head>
<meta charset="utf-8">
<title>BaFinn – Verpackungsdesign Wellness &amp; Sauna</title>
<link href="https://fonts.googleapis.com/css2?family=Montserrat:wght@600;700;800;900&display=swap" rel="stylesheet">
<style>
  :root {
    --bg: #e4e4e4;
    --label-white: #ffffff;
    --ink: #1c1c1c;
    --olive: #8a8a2e;
    --mint-text: #3f6b55;
    --berry-text: #b4262c;
    --spruce-dark: #1f4a1d;
    --spruce-light: #6e9a3a;
    --mint-dark: #1d3d2c;
    --mint-light: #4f8a5e;
    --berry-dark: #6e0d14;
    --berry-light: #c92a35;
  }
  * { box-sizing: border-box; margin: 0; padding: 0; }
  html, body { width: 1200px; height: 603px; overflow: hidden; }
  body {
    background: var(--bg);
    font-family: "Montserrat", sans-serif;
    position: relative;
  }
  .pack { position: absolute; overflow: hidden; }
  .photo { position: absolute; inset: 0; }
  .photo--spruce { background: radial-gradient(circle at 40% 30%, var(--spruce-light), var(--spruce-dark) 85%); }
  .photo--mint { background: linear-gradient(100deg, var(--mint-dark), var(--mint-light) 50%, var(--mint-dark)); }
  .photo--berry { background: linear-gradient(100deg, var(--berry-dark), var(--berry-light) 50%, var(--berry-dark)); }

  .plate {
    position: absolute;
    background: var(--label-white);
    display: flex; flex-direction: column; align-items: center;
    text-align: center;
  }
  .brand {
    position: absolute; left: 50%; transform: translateX(-50%);
    background: var(--label-white);
    border-radius: 50%;
    display: flex; align-items: flex-end; justify-content: center;
    font-weight: 700; color: var(--ink);
  }
  .product-name {
    font-weight: 900; color: var(--ink);
    letter-spacing: 0.03em; text-transform: uppercase; line-height: 1.15;
  }
  .product-sub {
    font-weight: 700; letter-spacing: 0.08em; text-transform: uppercase;
    line-height: 1.5;
  }

  /* Faltschachtel */
  .box { left: 174px; top: 163px; width: 124px; height: 320px; }
  .box .plate { left: 14px; top: 88px; width: 96px; height: 232px; }
  .box .brand { top: 64px; width: 40px; height: 40px; font-size: 7px; padding-bottom: 4px; }
  .box .product-name { font-size: 13px; margin-top: 84px; }
  .box .product-sub { font-size: 7.5px; color: var(--olive); margin-top: auto; margin-bottom: 30px; }

  /* Flaschenetikett */
  .bottle-label { left: 316px; top: 310px; width: 102px; height: 178px; }
  .bottle-label .plate { left: 8px; top: 46px; width: 86px; height: 132px; }
  .bottle-label .brand { top: 28px; width: 34px; height: 34px; font-size: 6px; padding-bottom: 3px; }
  .bottle-label .product-name { font-size: 11.5px; margin-top: 40px; }
  .bottle-label .product-sub { font-size: 6.5px; color: var(--olive); margin-top: auto; margin-bottom: 14px; }

  /* Tiegeletiketten */
  .jar-label { top: 390px; width: 220px; height: 88px; }
  .jar-label .plate { left: 12px; top: 40px; width: 196px; height: 48px; padding-top: 15px; }
  .jar-label .brand { top: 22px; width: 30px; height: 30px; font-size: 6px; padding-bottom: 3px; }
  .jar-label .product-name { font-size: 11.5px; white-space: nowrap; }
  .jar-label .product-sub { font-size: 6.5px; white-space: nowrap; margin-top: 2px; }
  .jar-label--menthol { left: 460px; }
  .jar-label--menthol .product-sub { color: var(--mint-text); }
  .jar-label--peeling { left: 702px; }
  .jar-label--peeling .product-sub { color: var(--berry-text); }
</style>
</head>
<body>

  <section class="pack box">
    <div class="photo photo--spruce" role="img" aria-label="Foto: frische Fichtenzweige"></div>
    <div class="plate">
      <h2 class="product-name">Nordische<br>Fichte</h2>
      <p class="product-sub">Aufguss<br>für die Sauna</p>
    </div>
    <div class="brand">BaFinn</div>
  </section>

  <section class="pack bottle-label">
    <div class="photo photo--spruce" role="img" aria-label="Foto: frische Fichtenzweige"></div>
    <div class="plate">
      <h2 class="product-name">Nordische<br>Fichte</h2>
      <p class="product-sub">Aufguss<br>für die Sauna</p>
    </div>
    <div class="brand">BaFinn</div>
  </section>

  <section class="pack jar-label jar-label--menthol">
    <div class="photo photo--mint" role="img" aria-label="Foto: Minzblätter"></div>
    <div class="plate">
      <h2 class="product-name">Mentholkristalle</h2>
      <p class="product-sub">Für die Sauna</p>
    </div>
    <div class="brand">BaFinn</div>
  </section>

  <section class="pack jar-label jar-label--peeling">
    <div class="photo photo--berry" role="img" aria-label="Foto: Granatapfelkerne"></div>
    <div class="plate">
      <h2 class="product-name">Granatapfel-Peeling</h2>
      <p class="product-sub">Meersalz für den Körper</p>
    </div>
    <div class="brand">BaFinn</div>
  </section>

</body>
</html>
```